Velk Partners Building Business Cards

We need a business card that reflects our business as "Solar Experts" in San Diego. Browse our website www.velkpartners.example our License needs to be displayed as "CSLB# 3867140" our phone number is (619) 555-0187

Save thousands on your electric bills and increase the value of your home while helping to protect the environment. Our solar installation experts will help you design the system that's right for you, using only the highest quality equipment that will look great and give you ideal performance. Our goal is to make you energy independent, and get your electric bill to 0.

Paul Osterby
(619) 555-0187
paul@velkpartners.example

Target Market(s)

Home owners in san diego looking for solar

Industry/Entity Type

Solar Energy

Contact Information for Business Card

Paul Osterby
(619) 555-0187
paul@velkpartners.example

Font styles to use
Other font styles liked:
• Use our logo font

Requirements
Must have
• License needs to be displayed as "CSLB# 3867140" our phone number is (619) 555-0187
Nice to have
• Real images of rooftop home solar in san diego
Should not have
• our business address

```html
<!DOCTYPE html>
<html lang="en">
<head>
<meta charset="utf-8">
<title>Velk Partners Building – Business Card</title>
<link rel="stylesheet" href="https://fonts.googleapis.com/css2?family=Crimson+Text:wght@600;700&display=swap">
<style>
  :root {
    --backdrop: #1f1f1f;
    --navy: #213c78;
    --navy-deep: #1c3468;
    --navy-soft: #2f4a85;
    --orange: #f4a51c;
    --white: #ffffff;
    --panel-blue: #3a5aa8;
    --panel-dark: #1d2f6a;
  }
  * { box-sizing: border-box; margin: 0; padding: 0; }
  html, body { width: 1189px; height: 1200px; overflow: hidden; }
  body {
    background: var(--backdrop);
    font-family: "Crimson Text", Georgia, serif;
    position: relative;
  }
  .card {
    position: absolute;
    left: 171px;
    width: 856px;
    height: 488px;
    box-shadow: 6px 8px 14px rgba(0,0,0,.55);
    overflow: hidden;
  }
  .card--front { top: 67px; background: var(--white); }
  .card--back {
    top: 626px;
    background: linear-gradient(160deg, var(--navy-soft) 0%, var(--navy) 55%, var(--navy-deep) 100%);
  }

  /* front header */
  .brand {
    position: absolute;
    display: flex;
    align-items: center;
    gap: 14px;
    font-weight: 700;
    white-space: nowrap;
  }
  .brand__dot { border-radius: 50%; background: var(--orange); flex: none; }
  .card--front .brand { left: 38px; top: 78px; color: var(--navy); font-size: 46px; }
  .card--front .brand__dot { width: 34px; height: 34px; }

  .contact {
    position: absolute;
    right: 48px;
    top: 44px;
    text-align: right;
    color: var(--navy);
    font-weight: 600;
  }
  .contact__name { font-size: 27px; font-weight: 700; letter-spacing: .5px; text-transform: uppercase; line-height: 1.1; }
  .contact__line { font-size: 21px; line-height: 1.3; }
  .contact__line--license { margin-top: 12px; }
  .label { color: var(--orange); }
  .accent-tab {
    position: absolute; right: 0; top: 46px;
    width: 15px; height: 38px; background: var(--orange);
  }
  .rule { position: absolute; left: 0; right: 0; top: 186px; height: 10px; background: var(--navy); }

  .gallery {
    position: absolute; left: 0; right: 0; top: 210px; height: 196px;
    display: flex; gap: 5px;
  }
  .gallery__photo { flex: 1; }
  .gallery__photo:nth-child(1) { background: linear-gradient(180deg, #c9a98a 0%, #b8b0a4 28%, var(--panel-dark) 45%, #2a3f86 100%); }
  .gallery__photo:nth-child(2) { background: linear-gradient(170deg, #5d7a4c 0%, #8e9aa6 18%, var(--panel-blue) 40%, #2e4ba0 100%); }
  .gallery__photo:nth-child(3) { background: linear-gradient(165deg, #8fb8e0 0%, #6f89c8 20%, var(--panel-blue) 50%, #1f3478 100%); }
  .gallery__photo:nth-child(4) { background: linear-gradient(170deg, #b7a18f 0%, #8da0c8 14%, #2f4a9c 45%, var(--panel-dark) 100%); }

  .footer-band {
    position: absolute; left: 0; right: 0; bottom: 0; height: 67px;
    background: var(--navy);
    color: var(--white);
    font-size: 23px; font-weight: 600;
    display: flex; align-items: center; justify-content: center; gap: 8px;
  }

  /* back */
  .card--back .brand {
    left: 50%; top: 190px; transform: translateX(-50%);
    color: var(--white); font-size: 60px;
  }
  .card--back .brand__dot { width: 44px; height: 44px; }
  .social {
    position: absolute; left: 50%; top: 333px; transform: translateX(-50%);
    display: flex; gap: 18px;
  }
  .social__slot { width: 35px; height: 35px; background: var(--white); border-radius: 2px; }
</style>
</head>
<body>
  <section class="card card--front">
    <div class="brand"><span class="brand__dot"></span>Velk Partners Building</div>
    <div class="contact">
      <p class="contact__name">Paul Osterby</p>
      <p class="contact__line contact__line--license">CSLB# 3867140</p>
      <p class="contact__line"><span class="label">Phone:</span> (619) 555-0187</p>
    </div>
    <div class="accent-tab"></div>
    <div class="rule"></div>
    <div class="gallery">
      <div class="gallery__photo" role="img" aria-label="Photo of rooftop solar panels on a flat roof"></div>
      <div class="gallery__photo" role="img" aria-label="Photo of solar panel rows on a tiled roof"></div>
      <div class="gallery__photo" role="img" aria-label="Photo of solar panels installed on a home roof"></div>
      <div class="gallery__photo" role="img" aria-label="Close-up photo of solar panels on a roof"></div>
    </div>
    <div class="footer-band">
      <span><span class="label">Email:</span> paul@velkpartners.example</span>
      <span>|</span>
      <span><span class="label">Website:</span> www.velkpartners.example</span>
    </div>
  </section>

  <section class="card card--back" role="img" aria-label="Faint photo of a solar-paneled roof behind the brand name">
    <div class="brand"><span class="brand__dot"></span>Velk Partners Building</div>
    <div class="social">
      <span class="social__slot"></span>
      <span class="social__slot"></span>
      <span class="social__slot"></span>
      <span class="social__slot"></span>
    </div>
  </section>
</body>
</html>
```